Webdesign für Reittherapeutin
Zielgruppe
Ich bin Reittherapeutin und biete auf unserem privaten Hof Reittherapie für Kinder, Jugendliche und Erwachsene an. Die Therapieeinheiten finden im Freien statt, also auf dem Sandplatz oder im Gelände. In der Reittherapie steht nicht das Reiten, sonden der Umgang und die Beziehung zum Pferd im Vordergrund.
Aufgabenstellung
Mir gefallen Designs in Naturtönen, welche auch gut zu meiner Tätigkeit passen. Ich habe bereits ein Logo, einen Namen (Wiesen erleben) und die Domaine (www.wiesen-erleben.ch) ebenso.

```html
<!DOCTYPE html>
<html lang="de">
<head>
<meta charset="utf-8">
<title>Wiesen erleben – Reittherapie</title>
<link href="https://fonts.googleapis.com/css2?family=Fira+Sans+Condensed:wght@300;400&family=Fira+Sans:wght@300;400&family=Parisienne&display=swap" rel="stylesheet">
<style>
:root{
  --sage:#bcc375;
  --sage-text:#b4bb6a;
  --brown:#6e625a;
  --teal:#2a9aa3;
  --paper:#edeaeb;
  --slate:#737373;
  --ink:#1a1a1a;
  --white:#ffffff;
  --black:#000000;
}
*{margin:0;padding:0;box-sizing:border-box}
html,body{width:1069px;height:1200px;overflow:hidden}
body{position:relative;background:var(--paper);font-family:"Fira Sans",sans-serif;color:var(--ink)}
.sidebar{position:absolute;left:0;top:0;width:182px;height:1200px;background:var(--sage)}
.brand{height:157px;background:var(--white);display:flex;flex-direction:column;align-items:center;justify-content:center;gap:12px}
.brand-dot{width:46px;height:46px;border-radius:50%;background:var(--teal)}
.brand-name{font-family:"Fira Sans Condensed",sans-serif;font-weight:300;font-size:24px;color:var(--brown)}
.main-nav{list-style:none;position:absolute;top:214px;left:0;width:160px;text-align:center}
.main-nav li{height:48px;font-family:"Fira Sans Condensed",sans-serif;font-weight:300;font-size:19px;color:var(--brown)}
.hero{position:absolute;left:182px;top:0;width:887px;height:320px;background:linear-gradient(180deg,#9dbbd8 0%,#c4d2dc 36%,#8f8a6e 44%,#7b7360 62%,#b2a994 100%)}
.hero-title{position:absolute;left:490px;top:224px;font-family:"Fira Sans Condensed",sans-serif;font-weight:400;font-size:60px;letter-spacing:2px;color:var(--white);line-height:1}
.hero-rule{position:absolute;left:494px;top:289px;width:250px;height:1px;background:var(--sage)}
.hero-sub{position:absolute;left:494px;top:294px;font-family:"Fira Sans",sans-serif;font-weight:300;font-size:13px;letter-spacing:1px;color:var(--white)}
.intro{position:absolute;left:182px;top:320px;width:887px;height:319px;background:var(--paper)}
.intro-text{position:absolute;left:65px;top:66px;width:300px;font-size:11px;letter-spacing:.6px;line-height:1.05}
.intro-text p{margin-bottom:11px}
.intro-sign{position:absolute;left:208px;top:200px;font-family:"Parisienne",cursive;font-size:21px;color:var(--ink)}
.intro-photo{position:absolute;left:458px;top:32px;width:378px;height:251px;background:linear-gradient(180deg,#9dbbd8 0%,#b6c4ce 35%,#8a8470 50%,#c8c1b2 100%)}
.offers{position:absolute;left:182px;top:639px;width:887px;height:310px;background:var(--slate)}
.offer{position:absolute;top:30px;width:220px;text-align:center;color:var(--white)}
.offer-icon{display:block;width:58px;height:58px;margin:0 auto}
.offer-icon--placeholder{border-radius:50%;background:rgba(255,255,255,.14)}
.offer h2{margin-top:18px;font-family:"Fira Sans Condensed",sans-serif;font-weight:400;font-size:20px;letter-spacing:1px}
.offer-rule{width:20px;height:1.5px;background:var(--sage);margin:8px auto 0}
.offer p{margin:36px auto 0;width:188px;text-align:left;hyphens:auto;-webkit-hyphens:auto;font-size:11px;letter-spacing:.5px;line-height:1.05;height:62px}
.btn{display:inline-flex;align-items:center;gap:14px;height:24px;padding:0 10px;border:1px solid var(--sage);font-family:"Fira Sans Condensed",sans-serif;font-size:10px;color:var(--sage-text);text-transform:uppercase;letter-spacing:.3px;white-space:nowrap}
.offer .btn{margin-top:22px}
.contact{position:absolute;left:182px;top:949px;width:887px;height:194px;background:var(--paper)}
.contact-photo{position:absolute;left:51px;top:46px;width:103px;height:116px;background:linear-gradient(180deg,#a7c0d9,#8d8b7c 55%,#2d3450)}
.contact-card{position:absolute;left:238px;top:15px;font-size:11px;letter-spacing:.5px;line-height:1.05}
.contact-role{font-family:"Fira Sans Condensed",sans-serif;font-size:18px;color:var(--sage-text);letter-spacing:0}
.contact-phone{margin-top:6px;font-family:"Fira Sans Condensed",sans-serif;font-size:17px;letter-spacing:0}
.contact-address{margin-top:10px;font-style:normal}
.contact-mail{margin-top:12px}
.contact .btn{margin-top:12px;height:23px;gap:8px;padding:0 6px;font-size:8px}
.contact-map{position:absolute;left:490px;top:21px;width:203px;height:135px;background:linear-gradient(120deg,#cfe4d6 0%,#e9ecee 30%,#f2f2f2 100%)}
.legal{position:absolute;left:182px;top:1143px;width:887px;height:57px;background:var(--black);color:var(--white);text-align:center;font-family:"Fira Sans Condensed",sans-serif;font-size:9px;text-transform:uppercase;padding-top:16px;line-height:16px}
.legal span{margin:0 3px}
</style>
</head>
<body>
<aside class="sidebar">
  <div class="brand">
    <div class="brand-dot"></div>
    <div class="brand-name">Wiesen erleben</div>
  </div>
  <ul class="main-nav">
    <li>Reittherapie</li>
    <li>Angebot</li>
    <li>Über mich</li>
    <li>Pferde</li>
    <li>Kontakt</li>
  </ul>
</aside>

<header class="hero" role="img" aria-label="Foto: Reiterin liegt entspannt auf einem schwarzen Pferd auf dem Sandplatz, Felder und Himmel im Hintergrund">
  <h1 class="hero-title">Reittherapie</h1>
  <div class="hero-rule"></div>
  <div class="hero-sub">Beziehung zwischen Mensch und Pferd</div>
</header>

<section class="intro">
  <div class="intro-text">
    <p>In entspannter Atmosphäre dem Pferd begegnen.</p>
    <p>Freude, Motivation und Erfolgsmomente erfahren.</p>
    <p>Entspannung und Ruhe in der Natur finden.</p>
    <p>All das möchte ich meinen Klienten bieten und mit auf den Weg geben.</p>
    <p style="margin-top:16px">Hab den Mut Dich zu melden!</p>
  </div>
  <div class="intro-sign">Ich freue mich auf Dich!</div>
  <div class="intro-photo" role="img" aria-label="Foto: Mädchen mit Reithelm streichelt den Kopf eines schwarz-weissen Pferdes"></div>
</section>

<section class="offers">
  <div class="offer" style="left:84px">
    <svg class="offer-icon" viewBox="0 0 58 58" role="img" aria-label="Symbol: Person">
      <circle cx="29" cy="14" r="11" fill="none" stroke="#fff" stroke-width="1.5"/>
      <path d="M3 56 A26 24 0 0 1 55 56 Z" fill="none" stroke="#fff" stroke-width="1.5"/>
    </svg>
    <h2>Erstgespräch</h2>
    <div class="offer-rule"></div>
    <p>Ein Erstgespräch vor dem Besuch der Reittherapie klärt viele offene Fragen.</p>
    <span class="btn"><span>&gt;</span><span>Mehr dazu</span></span>
  </div>
  <div class="offer" style="left:333px">
    <div class="offer-icon offer-icon--placeholder" role="img" aria-label="Symbol: Pferdekopf"></div>
    <h2>Schnupperstunde</h2>
    <div class="offer-rule"></div>
    <p>Die Schnupperstunde ist dafür da, mich, die Pferde und die Stallumgebung kennen zu lernen.</p>
    <span class="btn"><span>&gt;</span><span>Mehr dazu</span></span>
  </div>
  <div class="offer" style="left:592px">
    <div class="offer-icon offer-icon--placeholder" role="img" aria-label="Symbol: Reiterin auf Pferd"></div>
    <h2>Einzelstunde</h2>
    <div class="offer-rule"></div>
    <p>In der Einzelstunde wird an den gemeinsamen formulierten Förderzielen und Wünschen Schritt für Schritt gearbeitet.</p>
    <span class="btn"><span>&gt;</span><span>Mehr dazu</span></span>
  </div>
</section>

<section class="contact">
  <div class="contact-photo" role="img" aria-label="Foto: Reittherapeutin mit Pferd auf der Weide"></div>
  <div class="contact-card">
    <div class="contact-role">Reittherapeutin</div>
    <div class="contact-phone">0041 79 000 12 34</div>
    <address class="contact-address">Andrea Kessler<br>Mattenweg 7<br>8400 Feldbach</address>
    <div class="contact-mail">info@wiesen-erleben.ch</div>
    <span class="btn"><span>&gt;</span><span>Kontakt aufnehmen</span></span>
  </div>
  <div class="contact-map" role="img" aria-label="Karte: Lage des Hofes mit Fluss und Strassen"></div>
</section>

<footer class="legal">
  <div>Zahlungsbedingungen</div>
  <div><span>Impressum</span><span>Datenschutz</span><span>Sitemap</span></div>
</footer>
</body>
</html>
```